I need to make a car magnet

It needs to include the words "PLAVO TOUR" and "2026 MEMBER" as well as the attached silhouette of the golfer. The color scheme needs to be navy, red and white. The shape and dimensions are open for interpretation

```html
<!DOCTYPE html>
<html lang="en">
<head>
<meta charset="utf-8">
<title>PLAVO TOUR – 2026 Member Car Magnet</title>
<link rel="stylesheet" href="https://fonts.googleapis.com/css2?family=Exo+2:ital,wght@1,800;1,900&display=swap">
<style>
  :root {
    --navy: #1d2b5c;
    --navy-ray: #2e3d72;
    --red: #e32332;
    --white: #ffffff;
    --backdrop: #b1b1b1;
  }
  * { box-sizing: border-box; margin: 0; padding: 0; }
  html, body {
    width: 892px;
    height: 1200px;
    overflow: hidden;
    background: var(--backdrop);
  }
  .magnet {
    position: absolute;
    left: 46px;
    top: 400px;
    width: 800px;
    height: 400px;
    overflow: hidden;
    background:
      radial-gradient(ellipse 60% 70% at 40% 48%, var(--navy-ray) 0%, rgba(46,61,114,0.35) 45%, rgba(29,43,92,0) 75%),
      var(--navy);
    box-shadow: 0 2px 5px rgba(0,0,0,0.35);
    font-family: "Exo 2", sans-serif;
    font-style: italic;
  }
  .brand-word {
    position: absolute;
    line-height: 1;
    font-weight: 900;
    letter-spacing: 1px;
    text-shadow: 3px 3px 0 #16214a;
  }
  .brand-word--first {
    left: 32px;
    top: 36px;
    font-size: 112px;
    color: var(--red);
  }
  .brand-word--second {
    left: 112px;
    top: 140px;
    font-size: 104px;
    color: var(--white);
  }
  .member-tag {
    position: absolute;
    left: 104px;
    top: 274px;
    width: 380px;
    height: 50px;
    background: var(--red);
    transform: skewX(-8deg);
    display: flex;
    align-items: center;
    justify-content: center;
  }
  .member-tag__text {
    transform: skewX(8deg);
    color: var(--white);
    font-weight: 800;
    font-size: 34px;
    line-height: 1;
    letter-spacing: 0.5px;
  }
  .golfer-art {
    position: absolute;
    left: 525px;
    top: 8px;
    width: 245px;
    height: 362px;
    border-radius: 60px 60px 12px 12px;
    background: linear-gradient(180deg, rgba(255,255,255,0.92), rgba(255,255,255,0.8));
  }
  .turf-band {
    position: absolute;
    left: 0;
    right: 0;
    bottom: 0;
    height: 40px;
    background: var(--white);
  }
</style>
</head>
<body>
  <main class="magnet">
    <span class="brand-word brand-word--first">PLAVO</span>
    <span class="brand-word brand-word--second">TOUR</span>
    <div class="member-tag"><span class="member-tag__text">2026 MEMBER</span></div>
    <div class="golfer-art" role="img" aria-label="White silhouette of a golfer putting a ball"></div>
    <div class="turf-band"></div>
  </main>
</body>
</html>
```